Corvel Capital LLC

Need Professional Business cards for New Investment Fund

Target Market(s)

High Quality investors

Industry/Entity Type

Financial

Contact Information for Business Card

Phone Number +1 555 284 6190
Name Lukas Varenko
Title Fund Manager
email lv@FundCorvel.com
Website www.FundCorvel.com

Colors

Designer to choose colors to be used in the design.

Requirements
Must have
• Must have our Logo and all of the above. Must be made so lettering and loge can be raised

```html
<!DOCTYPE html>
<html lang="en">
<head>
<meta charset="utf-8">
<title>Tarnwell – Business Card</title>
<link href="https://fonts.googleapis.com/css2?family=Jost:wght@500&family=Roboto:wght@400;500&display=swap" rel="stylesheet">
<style>
  :root {
    --backdrop: #c9c9c9;
    --card-dark: #3b463d;
    --card-light: #f3f3f1;
    --brand-dark: #39443b;
    --brand-green: #86b82a;
    --band-dark: #3a473c;
    --text-light: #ffffff;
    --text-muted: #e4e8e2;
    --rule: rgba(255,255,255,0.75);
    --front-mark: #c4c8c3;
  }
  * { margin: 0; padding: 0; box-sizing: border-box; }
  html, body { width: 1200px; height: 1138px; overflow: hidden; }
  body {
    background: var(--backdrop);
    position: relative;
    font-family: "Roboto", Arial, sans-serif;
  }
  .card {
    position: absolute;
    left: 275px;
    width: 620px;
    height: 374px;
    border-radius: 16px;
    overflow: hidden;
  }
  .card--front { top: 186px; background: var(--card-dark); }
  .card--back { top: 608px; background: var(--card-light); }

  .front-name {
    position: absolute;
    inset: 0;
    display: flex;
    align-items: center;
    justify-content: center;
    font-family: "Jost", "Helvetica Neue", sans-serif;
    font-weight: 500;
    font-size: 58px;
    letter-spacing: 2px;
    color: var(--front-mark);
  }

  .back-name {
    position: absolute;
    left: 45px;
    top: 70px;
    font-family: "Jost", "Helvetica Neue", sans-serif;
    font-weight: 500;
    font-size: 38px;
    line-height: 1;
    letter-spacing: 1px;
    color: var(--brand-dark);
  }

  .info-band {
    position: absolute;
    left: 15px;
    top: 170px;
    width: 590px;
    height: 188px;
    background:
      radial-gradient(circle at 95% 15%, var(--brand-green) 0%, rgba(134,184,42,0.55) 28%, rgba(58,71,60,0) 62%),
      var(--band-dark);
    color: var(--text-light);
  }
  .person-name {
    position: absolute;
    left: 30px;
    top: 20px;
    font-weight: 500;
    font-size: 24px;
    line-height: 1.2;
  }
  .person-title {
    position: absolute;
    left: 30px;
    top: 55px;
    font-size: 16px;
    line-height: 1.2;
    color: var(--text-muted);
  }
  .contact-list {
    position: absolute;
    left: 30px;
    top: 96px;
    width: 308px;
    list-style: none;
  }
  .contact-item {
    display: flex;
    align-items: center;
    gap: 18px;
    height: 26px;
    font-size: 15px;
    border-bottom: 1px solid var(--rule);
  }
  .contact-item:last-child { border-bottom: none; }
  .contact-icon { width: 14px; height: 14px; flex: none; }

  .band-name {
    position: absolute;
    right: 30px;
    top: 72px;
    font-family: "Jost", "Helvetica Neue", sans-serif;
    font-weight: 500;
    font-size: 34px;
    line-height: 1;
    color: var(--text-light);
  }
</style>
</head>
<body>
  <section class="card card--front">
    <div class="front-name">TARNWELL</div>
  </section>

  <section class="card card--back">
    <div class="back-name">TARNWELL</div>

    <div class="info-band">
      <div class="person-name">Lukas Varenko</div>
      <div class="person-title">Fund Manager</div>
      <ul class="contact-list">
        <li class="contact-item">
          <svg class="contact-icon" viewBox="0 0 16 16" aria-hidden="true"><path fill="#fff" d="M3 2l3 0 1 4-2 1c1 2 2 3 4 4l1-2 4 1v3c-6 1-12-5-11-11z"/></svg>
          <span>+1 555 284 6190</span>
        </li>
        <li class="contact-item">
          <svg class="contact-icon" viewBox="0 0 16 16" aria-hidden="true"><rect x="1" y="3" width="14" height="10" fill="#fff"/><path d="M1 3l7 6 7-6" fill="none" stroke="#3a473c" stroke-width="1.4"/></svg>
          <span>lv@FundCorvel.com</span>
        </li>
        <li class="contact-item">
          <svg class="contact-icon" viewBox="0 0 16 16" aria-hidden="true"><circle cx="8" cy="8" r="6.5" fill="none" stroke="#fff" stroke-width="1.4"/><path d="M1.5 8h13M8 1.5c-3 3.5-3 9.5 0 13M8 1.5c3 3.5 3 9.5 0 13" fill="none" stroke="#fff" stroke-width="1.2"/></svg>
          <span>www.FundCorvel.com</span>
        </li>
      </ul>
      <div class="band-name">TARNWELL</div>
    </div>
  </section>
</body>
</html>
```